Business Intelligence Application - Reporting Menu and Report Criteria Design

Looking for a fresh, effective and user friendly view for the menu structure and reporting criteria screen format for a business reporting application. Initial format completed, content structure is in place, but we need the 'wow' design.. as its a serious professional report/BI tool it has to fall within certain guidelines for clarity and graphics..but we want it to be slick, friendly, great user experience. There is a large amount of complex content to fit into a small space and we need it to be very inviting, modern and intuitive.. If interested, please review the attachment. We have live screens in operation, but feel these could be improved and looking forward to seeing what great creative suggestions could be made. Please review work done to date in the attached.. We are not looking for a total re-design of everything, all the basic business content/structure is there.. but tell us what we could do to improve this in terms of graphic design... particularly the criteria screens.. thanks!
Updates

Reason: Need a few more days to review designs - thanks for all submissions so far, we will make a selection shortly.

Target Market(s)

Business analysts, hotel operations teams, finance analysts hospitality industry

Industry/Entity Type

Hospitality

Coding

Coded - Design and coding required

Number of Pages Required

4 page

Font styles to use
Sans Serif
Other font styles liked:
• Candara, please see example in deck

Colors
3276b5
3176b5
0255a3
85acd3
33a6d7
cee9f5
85cae6

Requirements
Must have
• sharp clear, logical menu structure, (currently it has 'clicks to sub-menus, we need hover over, slide to sub-menus..) colour, styling.. and most focus on revision of criteria.. right now is somewhat heavy, cumbersome.. keep colour and friendly intuitive process steps.. its heavy analytical stuff.. best of luck!
Should not have
• No grey fonts on white or grey screens! many business apps are not readable or sharp.. or fonts are too small.. colourless, so please avoid that.. see our deck - sharp dark (navy) or black fonts on white, or light shading..

```html
<!DOCTYPE html>
<html lang="en">
<head>
<meta charset="utf-8">
<title>Yieldline – Admin Setup</title>
<link rel="stylesheet" href="https://fonts.googleapis.com/css2?family=Open+Sans:wght@400;600&family=Raleway:wght@400;500&display=swap">
<style>
:root{
  --navy:#0255a3;
  --sky:#35a3da;
  --modal-band:#2a5e92;
  --dim:#c6c6c6;
  --panel:#d0d0d0;
  --field:#c9c9c9;
  --field-line:#b4b4b4;
  --menu-bg:#f7f7f7;
  --menu-active:#ececec;
  --menu-line:#dcdcdc;
  --text-dark:#1f2a36;
  --label:#3a3a3a;
  --accent:#4fa6d9;
}
*{box-sizing:border-box;margin:0;padding:0}
html,body{width:1200px;height:866px;overflow:hidden}
body{position:relative;background:var(--dim);font-family:"Open Sans",sans-serif;color:var(--text-dark)}

.sidebar{position:absolute;left:0;top:0;width:315px;height:866px;background:var(--navy)}
.brand{position:absolute;left:36px;top:32px;display:flex;align-items:center;gap:12px;color:#fff;font-size:36px;font-weight:600}
.brand-mark{width:30px;height:30px;border-radius:50%;background:#fff}
.nav{position:absolute;top:110px;left:0;width:315px;list-style:none}
.nav li{display:flex;align-items:center;border-bottom:1px solid rgba(255,255,255,.14);color:#fff;font-size:15px;font-weight:600;letter-spacing:.2px}
.nav li.active{background:var(--sky)}
.nav .ico{width:66px;height:100%;display:flex;align-items:center;justify-content:center;border-right:1px solid rgba(255,255,255,.14)}
.nav .label{flex:1;padding-left:17px}
.nav .chev{width:40px;text-align:center;font-size:18px}

.topbar{position:absolute;left:315px;top:0;right:0;height:95px;border-bottom:1px solid #b7b7b7}
.welcome{position:absolute;left:367px;top:31px;font-family:"Raleway",sans-serif;font-size:21px;color:#333}
.date{position:absolute;left:545px;top:36px;font-family:"Raleway",sans-serif;font-size:16px;color:#333}
.round-btn{position:absolute;top:27px;width:35px;height:35px;border:1.5px solid #444;border-radius:50%;display:flex;align-items:center;justify-content:center}

.modal{position:absolute;left:392px;top:141px;width:747px;height:621px;background:var(--panel);box-shadow:0 1px 3px rgba(0,0,0,.2)}
.modal-head{height:53px;background:var(--modal-band);color:#fff;font-size:17px;display:flex;align-items:center;padding-left:150px}
.modal-close{position:absolute;right:16px;top:14px}
.row-label{position:absolute;left:48px;font-size:16px;color:var(--label)}
.field{position:absolute;left:194px;width:443px;height:44px;background:var(--field);border:1px solid var(--field-line);border-radius:2px}
.field .arrow{position:absolute;right:14px;top:12px;font-size:12px;color:#333}

.dropdown{position:absolute;background:var(--menu-bg);border:1px solid var(--accent);list-style:none}
.dropdown li{height:51px;display:flex;align-items:center;padding-left:28px;font-family:"Raleway",sans-serif;font-size:18px;color:#222;border-bottom:1px solid var(--menu-line);position:relative}
.dropdown li:last-child{border-bottom:none}
.dropdown li.open{background:var(--menu-active)}
.dropdown li .more{position:absolute;right:26px;font-size:16px}
.menu-admin{left:320px;top:110px;width:226px}
.menu-setup{left:548px;top:212px;width:226px}
.menu-setup li{height:52px}

.copyright{position:absolute;left:0;width:1470px;top:810px;text-align:center;font-size:13px;color:#222}
.build{position:absolute;left:1169px;top:819px;font-size:10px;color:#333}
</style>
</head>
<body>

<aside class="sidebar">
  <div class="brand"><span class="brand-mark"></span>Yieldline</div>
  <ul class="nav">
    <li class="active" style="height:58px">
      <span class="ico"><svg width="26" height="28" viewBox="0 0 26 28"><circle cx="13" cy="8" r="7" fill="#fff"/><path d="M0 28v-6c0-4 4-7 8-7h10c4 0 8 3 8 7v6z" fill="#fff"/></svg></span>
      <span class="label">ADMIN</span><span class="chev">›</span></li>
    <li style="height:59px">
      <span class="ico"><svg width="28" height="28" viewBox="0 0 28 28"><g fill="#fff"><circle cx="14" cy="14" r="9"/><rect x="11" y="0" width="6" height="28" rx="1"/><rect x="0" y="11" width="28" height="6" rx="1"/><rect x="11" y="0" width="6" height="28" rx="1" transform="rotate(45 14 14)"/><rect x="11" y="0" width="6" height="28" rx="1" transform="rotate(-45 14 14)"/></g><circle cx="14" cy="14" r="4" fill="#0255a3"/></svg></span>
      <span class="label">MANAGEMENT</span><span class="chev">›</span></li>
    <li style="height:54px">
      <span class="ico"><svg width="26" height="26" viewBox="0 0 26 26"><circle cx="10" cy="10" r="7.5" fill="none" stroke="#fff" stroke-width="3.5"/><path d="M15.5 15.5L24 24" stroke="#fff" stroke-width="4.5" stroke-linecap="round"/></svg></span>
      <span class="label">PROPERTY SEARCH</span><span class="chev">›</span></li>
    <li style="height:58px">
      <span class="ico"><svg width="28" height="28" viewBox="0 0 28 28"><rect x="5" y="5" width="18" height="18" fill="#fff"/><rect x="9" y="9" width="10" height="10" fill="#0255a3"/><rect x="11" y="11" width="6" height="6" fill="#fff"/><g stroke="#fff" stroke-width="1.5"><path d="M8 1v3M12 1v3M16 1v3M20 1v3M8 24v3M12 24v3M16 24v3M20 24v3M1 8h3M1 12h3M1 16h3M1 20h3M24 8h3M24 12h3M24 16h3M24 20h3"/></g></svg></span>
      <span class="label">INTEL</span><span class="chev">›</span></li>
    <li style="height:62px">
      <span class="ico"><svg width="28" height="26" viewBox="0 0 28 26"><g fill="#fff"><rect x="10" y="0" width="8" height="7"/><rect x="0" y="17" width="8" height="8"/><rect x="10" y="17" width="8" height="8"/><rect x="20" y="17" width="8" height="8"/></g><path d="M14 7v10M4 17v-5h20v5" stroke="#fff" stroke-width="2" fill="none"/></svg></span>
      <span class="label">PLANNING</span><span class="chev">›</span></li>
  </ul>
</aside>

<header class="topbar">
  <div class="welcome">Welcome Admin</div>
  <div class="date">Tuesda October 03 ,2017 <sup style="font-size:9px">*</sup></div>
  <div class="round-btn" style="left:760px"><svg width="18" height="20" viewBox="0 0 18 20"><path d="M9 1c-4 0-6 3-6 6v5l-2 3h16l-2-3V7c0-3-2-6-6-6z" fill="#333"/><circle cx="9" cy="17.5" r="2.3" fill="#333"/></svg></div>
  <div class="round-btn" style="left:803px"><svg width="20" height="20" viewBox="0 0 20 20"><path d="M6 4.5a7 7 0 1 0 8 0" fill="none" stroke="#333" stroke-width="2.6" stroke-linecap="round"/><path d="M10 1v8" stroke="#333" stroke-width="2.6" stroke-linecap="round"/></svg></div>
</header>

<section class="modal">
  <div class="modal-head">PROPERTY SEARCH</div>
  <svg class="modal-close" width="22" height="22" viewBox="0 0 22 22"><path d="M3 3l16 16M19 3L3 19" stroke="#fff" stroke-width="5" stroke-linecap="round"/></svg>

  <div class="field" style="top:90px"></div>
  <div class="field" style="top:133px"></div>
  <div class="row-label" style="top:203px">Search ID :</div>
  <div class="field" style="top:192px"></div>
  <div class="row-label" style="top:263px">Search Product :</div>
  <div class="field" style="top:252px"></div>
  <div class="row-label" style="top:323px">Divisions :</div>
  <div class="field" style="top:312px"><span class="arrow">⌄</span></div>
  <div class="field" style="top:355px"><span class="arrow">»</span></div>
  <div class="field" style="top:398px"><span class="arrow">»</span></div>
  <div class="row-label" style="top:469px">Regions :</div>
  <div class="field" style="top:458px"></div>
  <div class="row-label" style="top:529px">Areas :</div>
  <div class="field" style="top:518px"></div>
</section>

<ul class="dropdown menu-admin">
  <li>Registration</li>
  <li>User Access</li>
  <li class="open">Setup<span class="more">»</span></li>
  <li>Data imports</li>
</ul>

<ul class="dropdown menu-setup">
  <li>Market Segments</li>
  <li>Banquet &amp; Catering</li>
  <li>Outlets/F&amp;B Service</li>
  <li>Other Income</li>
  <li>Impact Dates</li>
  <li>Inventory</li>
  <li>Geo/Location</li>
  <li>Distribution Channels</li>
</ul>

<div class="copyright">Copyright © 2017 Yieldline. All Rights Reserved.</div>
<div class="build">C7</div>

</body>
</html>
```